CLAIM SHIELD

I'm virtually ready to launch my site, but I have a number of edits and modifications that need to be implemented. More importantly, I'm always looking to improve my site, particularly now that I am making my proverbial "FIRST IMPRESSION." Thus, I'm willing to see if there is someone who can add creativity and perhaps improve what I already have, particularly on the All Important Front Page.

```html
<!DOCTYPE html>
<html lang="en">
<head>
<meta charset="utf-8">
<title>Claim Shield – Home</title>
<link href="https://fonts.googleapis.com/css2?family=Lato:wght@400;700;900&family=Open+Sans:wght@600;700;800&display=swap" rel="stylesheet">
<style>
:root{
  --navy:#0c2252;
  --navy-deep:#071a40;
  --red:#a8001b;
  --red-text:#b3111e;
  --ink:#222;
  --muted:#444;
  --light:#eef0f8;
  --white:#fff;
  --line:#c9ccd6;
}
*{box-sizing:border-box;margin:0;padding:0}
html,body{width:1200px;height:3778px;overflow:hidden}
body{position:relative;font-family:'Lato',sans-serif;color:var(--ink);background:var(--white)}
.heading{font-family:'Open Sans',sans-serif;font-weight:700;letter-spacing:-.5px}
.btn{position:absolute;display:flex;align-items:center;justify-content:center;border-radius:30px;font-family:'Lato',sans-serif;font-weight:900;letter-spacing:.5px}
.btn-white{background:var(--white);color:var(--red-text)}
.btn-navy{background:var(--navy);color:var(--white);box-shadow:3px 4px 0 var(--red)}
.mark-dot{position:absolute;width:36px;height:36px;border-radius:50%;background:var(--red);border:4px solid #fff;box-shadow:0 0 0 2px var(--navy)}

/* hero */
.hero{position:absolute;left:0;top:0;width:1200px;height:692px;background:linear-gradient(90deg,#0b2454 0%,#13264f 40%,#3a2a2a 70%,#5a2a22 100%);overflow:hidden}
.hero-photo{position:absolute;left:520px;top:0;width:680px;height:692px;background:radial-gradient(ellipse at 55% 55%,#2c3b5a 0%,#3a2b25 45%,rgba(60,30,25,0) 75%)}
.topbar{position:absolute;left:741px;top:0;width:459px;height:51px;background:var(--white);display:flex;align-items:center;padding-left:18px;gap:16px}
.topbar small{font-size:11px;font-weight:700;color:var(--navy)}
.topbar b{font-size:24px;color:var(--red-text);font-weight:900}
.logo-tab{position:absolute;left:111px;top:0;width:172px;height:161px;background:var(--white);border-radius:0 0 86px 86px;display:flex;align-items:center;justify-content:center}
.logo-tab span{width:138px;height:138px;border-radius:50%;background:var(--white);border:3px solid var(--red);display:flex;align-items:center;justify-content:center;text-align:center;font-family:'Open Sans',sans-serif;font-weight:800;font-size:17px;color:var(--red)}
.nav{position:absolute;top:86px;font-size:15px;font-weight:700;color:var(--white)}
.welcome{position:absolute;left:111px;top:270px;font-size:25px;color:var(--white);letter-spacing:1px}
.hero h1{position:absolute;left:109px;top:312px;font-size:51px;color:var(--white);font-weight:800;letter-spacing:1px}
.hero p{position:absolute;left:112px;top:388px;width:420px;font-size:12.5px;line-height:30px;color:var(--white)}

/* review form */
.review{position:absolute;left:0;top:692px;width:534px;height:671px;background:var(--red)}
.review h2{position:absolute;left:0;width:534px;top:36px;text-align:center;color:var(--white);font-size:30px;font-weight:800}
.review .lead{position:absolute;left:20px;width:494px;top:88px;text-align:center;color:var(--white);font-size:13px;font-weight:700;line-height:29px}
.field{position:absolute;left:35px;width:462px;background:var(--white);font-size:15px;color:#222;padding:0 18px;display:flex;justify-content:space-between;align-items:center}
.field.msg{align-items:flex-start;padding-top:20px}
.field svg{width:20px;height:20px;fill:#c2c4c9}
.submit{left:35px;top:1264px;width:472px;height:55px;font-size:17px}

/* about */
.about h2{position:absolute;left:620px;top:828px;font-size:36px;color:var(--navy);font-weight:800}
.about h2 em{font-style:normal;color:var(--red-text)}
.about p{position:absolute;left:620px;width:467px;text-align:justify;color:var(--muted)}
.about .p1{top:879px;font-size:15px;line-height:29px}
.about .p2{top:1035px;font-size:13.4px;line-height:29px}
.about .p3{top:1209px;font-size:13.4px;line-height:29px}
.readmore{left:622px;top:1314px;width:157px;height:47px;font-size:15px}
.call{position:absolute;left:830px;top:1305px;display:flex;align-items:center;gap:12px}
.call .ring{width:58px;height:58px;border-radius:50%;border:2px solid var(--navy);display:flex;align-items:center;justify-content:center}
.call small{display:block;color:var(--red-text);font-weight:900;font-size:15px}
.call b{display:block;color:var(--red-text);font-size:26px;font-weight:900}

/* services */
.services{position:absolute;left:0;top:1455px;width:1200px;height:628px;background:var(--light)}
.center-title{position:absolute;left:0;width:1200px;text-align:center;font-size:36px;font-weight:800;color:var(--navy)}
.center-title em{font-style:normal;color:var(--red-text)}
.services .intro{position:absolute;left:225px;width:750px;top:157px;text-align:center;font-size:14.5px;line-height:30px;color:#222}
.hex{position:absolute}
.hex-label{position:absolute;width:260px;text-align:center;font-size:16.5px;font-weight:700;line-height:29px;color:#111}
.arrow{position:absolute;width:28px;height:28px;border-radius:50%;background:#111;display:flex;align-items:center;justify-content:center}

/* contact band */
.band{position:absolute;left:0;top:2083px;width:1200px;height:565px;background:linear-gradient(90deg,#0b1d45 0%,#2a1d3d 40%,#6b0c20 75%,#94061b 100%)}
.band h2{position:absolute;left:0;width:1200px;top:124px;text-align:center;font-size:35px;font-weight:800;color:var(--white)}
.band p{position:absolute;left:155px;width:890px;text-align:center;font-size:15px;line-height:31px;color:var(--white)}
.band .btn{left:446px;top:431px;width:304px;height:46px;font-size:15px}

/* faq */
.faq-item{position:absolute;left:110px;width:976px;border:2px solid var(--line);border-radius:34px;display:flex;align-items:center;padding:0 30px;font-size:20px;color:#222}
.faq-item .q{flex:1;display:flex;gap:14px;line-height:29px}
.plus{width:34px;height:34px;background:#111;border-radius:3px;display:flex;align-items:center;justify-content:center}

/* footer */
.footer{position:absolute;left:0;top:3352px;width:1200px;height:426px;background:var(--navy)}
.foot-logo{position:absolute;left:114px;top:72px;width:188px;height:188px;border-radius:50%;background:var(--white);border:4px solid var(--red);display:flex;align-items:center;justify-content:center;font-family:'Open Sans',sans-serif;font-weight:800;font-size:22px;color:var(--red);text-align:center}
.foot-col{position:absolute;top:68px;color:var(--white)}
.foot-col h3{font-family:'Lato',sans-serif;font-weight:400;font-size:21px;margin-bottom:12px}
.foot-col li{list-style:none;font-size:14px;height:34.5px;display:flex;align-items:center;gap:8px}
.foot-col li i{width:12px;height:12px;border-radius:50%;background:var(--white);display:inline-block}
.contact-row{display:flex;gap:14px;font-size:14.5px;line-height:28px;margin-bottom:10px}
.contact-row .ic{width:30px;height:30px;border-radius:50%;background:var(--white);flex:none;display:flex;align-items:center;justify-content:center}
.footer hr{position:absolute;left:110px;top:333px;width:977px;border:0;border-top:1px solid #8a96b5}
.copy{position:absolute;left:108px;top:370px;font-size:14.5px;font-weight:700;color:var(--white)}
.social{position:absolute;top:367px;width:32px;height:32px;border-radius:50%;background:var(--white)}
</style>
</head>
<body>

<section class="hero">
  <div class="hero-photo" role="img" aria-label="Smiling attorney in a navy suit standing in a law library"></div>
  <div class="topbar"><small>TEXT / CONTACT US TODAY.</small><b>480.555.0142</b></div>
  <div class="logo-tab"><span>Claim<br>Shield</span></div>
  <span class="nav" style="left:455px">HOME</span>
  <span class="nav" style="left:557px">ABOUT US</span>
  <span class="nav" style="left:695px">PRACTICE AREAS</span>
  <span class="nav" style="left:882px">FAQ</span>
  <div class="btn btn-white" style="left:943px;top:73px;width:145px;height:47px;font-size:14px">CONTACT US</div>
  <div class="welcome">WELCOME TO</div>
  <h1 class="heading">CLAIM SHIELD</h1>
  <p>BUSINESS OWNERS: Claim Shield (CS) Is An Extremely Affordable Legal Service Plan (As Little As $8.00 Per Month) That INSULATES Business Owners From Unwarranted LEGAL CLAIMS And Expensive LAWSUITS.</p>
  <div class="btn btn-white" style="left:111px;top:530px;width:304px;height:45px;font-size:15px">SCHEDULE FREE CONSULTATION</div>
</section>

<section class="review">
  <h2 class="heading">GET A FREE CASE REVIEW</h2>
  <div class="lead">Our Plan Uses Local, Experienced, Quality Attorneys Who Focus On PROBLEM PREVENTION Using Proprietary Tools Available Only To CS Members.</div>
</section>
<div class="field" style="top:867px;height:59px">Name<svg viewBox="0 0 20 20"><circle cx="10" cy="6" r="4.5"/><path d="M2 19c0-5 4-7 8-7s8 2 8 7z"/></svg></div>
<div class="field" style="top:940px;height:59px">Phone Number<svg viewBox="0 0 20 20"><path d="M5 2l3 4-2 2c1 3 3 5 6 6l2-2 4 3-2 3C9 18 2 11 2 4z"/></svg></div>
<div class="field" style="top:1014px;height:58px">Email Address<svg viewBox="0 0 20 20"><path d="M2 4h16v12H2z M2 4l8 6 8-6" /></svg></div>
<div class="field msg" style="top:1087px;height:154px">Message<svg viewBox="0 0 20 20"><path d="M1 3h12v8H6l-3 3v-3H1z M15 6h4v8h-2v3l-3-3H8v-2h7z"/></svg></div>
<div class="btn btn-navy submit" style="box-shadow:none">SUBMIT</div>

<section class="about">
  <span class="mark-dot" style="left:622px;top:786px"></span>
  <h2 class="heading">ABOUT <em>CLAIM SHIELD</em></h2>
  <p class="p1">CS is a group of attorney and legal assistants with many years of experience in litigation, who are devoted to PREVENTING LEGAL CLAIMS and COSTLY LAWSUITS through a variety of FREE and VERY AFFORDABLE services described below. OUR UNIQUE SERVICE PLAN MAKES IT POSSIBLE FOR US TO SHIELD YOUR BUSINESS.</p>
  <p class="p2">A homebuilding company was sued by a former employee who claimed to have been promised a more favorable sales area, which claim was disputed by the homebuilder. There was no evidence that such a promise had been made, other than the plaintiff's oral testimony. The company had the case dismissed, but spent $10,000 defending the case.</p>
  <p class="p3">And even though it was awarded its attorney's fees, the plaintiff proved uncollectible. Had the company been a CS member, the case likely would never have been filed.</p>
  <div class="btn btn-navy readmore">READ MORE</div>
  <div class="call">
    <div class="ring"><svg width="30" height="30" viewBox="0 0 20 20"><path d="M5 2l3 4-2 2c1 3 3 5 6 6l2-2 4 3-2 3C9 18 2 11 2 4z" fill="none" stroke="#a8001b" stroke-width="1.4"/></svg></div>
    <div><small>CALL TODAY</small><b>800.555.0199</b></div>
  </div>
</section>

<section class="services">
  <span class="mark-dot" style="left:583px;top:53px"></span>
  <h2 class="center-title heading" style="top:96px">OUR <em>SERVICES</em></h2>
  <p class="intro">The price for a membership is a ridiculously low $9.95 PER WEEK. We believe that this fee is very affordable. So what is it? Membership includes the following:</p>

  <svg class="hex" style="left:109px;top:257px" width="230" height="203" viewBox="0 0 230 203" role="img" aria-label="Three colleagues reviewing a laptop in an office">
    <defs><linearGradient id="g1" x1="0" y1="0" x2="0" y2="1"><stop offset="0" stop-color="#dfe3e8"/><stop offset="1" stop-color="#8a8f98"/></linearGradient></defs>
    <polygon points="57,2 173,2 228,101 173,201 57,201 2,101" fill="url(#g1)" stroke="#0c2252" stroke-width="3"/>
  </svg>
  <div class="hex-label" style="left:94px;top:478px">FREE<br>INITIAL CONSULTATION</div>

  <svg class="hex" style="left:415px;top:238px" width="356" height="316" viewBox="0 0 356 316" role="img" aria-label="Two lawyers reviewing a document at a desk">
    <defs>
      <linearGradient id="g2" x1="0" y1="0" x2="0" y2="1"><stop offset="0" stop-color="#c7ccd3"/><stop offset="1" stop-color="#6d6a66"/></linearGradient>
      <clipPath id="hx"><polygon points="88,2 268,2 354,158 268,314 88,314 2,158"/></clipPath>
    </defs>
    <polygon points="88,2 268,2 354,158 268,314 88,314 2,158" fill="url(#g2)"/>
    <path d="M0 245 Q178 200 356 245 V316 H0 Z" fill="#a8001b" clip-path="url(#hx)"/>
    <polygon points="88,2 268,2 354,158 268,314 88,314 2,158" fill="none" stroke="#0c2252" stroke-width="3"/>
    <text x="178" y="259" text-anchor="middle" fill="#fff" font-family="Lato,sans-serif" font-weight="700" font-size="16.5">PROPRIETARY</text>
    <text x="178" y="288" text-anchor="middle" fill="#fff" font-family="Lato,sans-serif" font-weight="700" font-size="16.5">CONTRACT LANGUAGE</text>
  </svg>

  <svg class="hex" style="left:858px;top:257px" width="230" height="203" viewBox="0 0 230 203" role="img" aria-label="Attorney in a suit seated at a desk">
    <defs><linearGradient id="g3" x1="0" y1="0" x2="0" y2="1"><stop offset="0" stop-color="#cfd5dc"/><stop offset="1" stop-color="#3f5170"/></linearGradient></defs>
    <polygon points="57,2 173,2 228,101 173,201 57,201 2,101" fill="url(#g3)" stroke="#0c2252" stroke-width="3"/>
  </svg>
  <div class="hex-label" style="left:843px;top:478px">FREE<br>CONSULTATION</div>

  <div class="arrow" style="left:44px;top:379px"><svg width="12" height="12" viewBox="0 0 12 12"><path d="M8 1L3 6l5 5" stroke="#fff" stroke-width="2" fill="none"/></svg></div>
  <div class="arrow" style="left:1133px;top:379px"><svg width="12" height="12" viewBox="0 0 12 12"><path d="M4 1l5 5-5 5" stroke="#fff" stroke-width="2" fill="none"/></svg></div>
</section>

<section class="band" role="img" aria-label="Dim courtroom interior tinted navy to red">
  <span class="mark-dot" style="left:583px;top:64px"></span>
  <h2 class="heading">CONTACT US FOR A FREE CONSULTATION</h2>
  <p style="top:183px">In our vast experience with commercial litigation, we believe that a very large percentage of litigation cases hinge on "he said / she said" issues. By using CS's services, we believe we can INSULATE you and your business from all such issues, which will MINIMIZE your EXPOSURE to LEGAL CLAIMS and LAWSUITS.</p>
  <p style="top:307px">Call for your FREE CONSULTATION and let us show you why the plaintiff likely would not have found a contingency attorney (as was the case) or been able to pay an attorney on an hourly basis. In short, by using CS's services, the plaintiff's claim would not have been filed.</p>
  <div class="btn btn-white">FREE CONSULATION CONTACT US</div>
</section>

<section class="faq">
  <span class="mark-dot" style="left:583px;top:2705px"></span>
  <h2 class="center-title heading" style="top:2755px">FREQUENTLY <em>ASKED QUESTIONS</em></h2>
  <div class="faq-item" style="top:2838px;height:67px"><div class="q"><span>→</span><span>Why should I be concerned about legal claims?</span></div><span class="plus"><svg width="14" height="14"><path d="M7 1v12M1 7h12" stroke="#fff" stroke-width="3"/></svg></span></div>
  <div class="faq-item" style="top:2924px;height:66px"><div class="q"><span>→</span><span>Provide more details about the value of CS's contract language.</span></div><span class="plus"><svg width="14" height="14"><path d="M7 1v12M1 7h12" stroke="#fff" stroke-width="3"/></svg></span></div>
  <div class="faq-item" style="top:3010px;height:87px"><div class="q"><span>→</span><span>If I'm a contractor, for example, how can a CS membership minimize legal claims<br>against my business?</span></div><span class="plus"><svg width="14" height="14"><path d="M7 1v12M1 7h12" stroke="#fff" stroke-width="3"/></svg></span></div>
  <div class="faq-item" style="top:3116px;height:66px"><div class="q"><span>→</span><span>What does a CS membership cost?</span></div><span class="plus"><svg width="14" height="14"><path d="M7 1v12M1 7h12" stroke="#fff" stroke-width="3"/></svg></span></div>
  <div class="faq-item" style="top:3201px;height:67px"><div class="q"><span>→</span><span>Do you have a Referral Program?</span></div><span class="plus"><svg width="14" height="14"><path d="M7 1v12M1 7h12" stroke="#fff" stroke-width="3"/></svg></span></div>
</section>

<footer class="footer">
  <div class="foot-logo">Claim<br>Shield</div>
  <div class="foot-col" style="left:378px"><h3>QUICK LINKS</h3><ul>
    <li><i></i>Home</li><li><i></i>About</li><li><i></i>Practice Areas</li><li><i></i>Testimonials</li><li><i></i>Contact Us</li></ul></div>
  <div class="foot-col" style="left:601px"><h3>HELP LINKS</h3><ul>
    <li><i></i>FAQ</li><li><i></i>Terms of use</li><li><i></i>Privacy Policy</li><li><i></i>Support Links</li><li><i></i>Conditions</li></ul></div>
  <div class="foot-col" style="left:804px"><h3>CONTACT US</h3>
    <div class="contact-row"><span class="ic"><svg width="14" height="16" viewBox="0 0 14 16"><path d="M7 0a6 6 0 0 0-6 6c0 4 6 10 6 10s6-6 6-10a6 6 0 0 0-6-6zm0 8a2 2 0 1 1 0-4 2 2 0 0 1 0 4z" fill="#0c2252"/></svg></span><span>2450 Oak Ridge Ave., Suite 210<br>Springfield, Arizona 85001</span></div>
    <div class="contact-row"><span class="ic"><svg width="14" height="14" viewBox="0 0 20 20"><path d="M5 2l3 4-2 2c1 3 3 5 6 6l2-2 4 3-2 3C9 18 2 11 2 4z" fill="#0c2252"/></svg></span><span>480.555.0142</span></div>
    <div class="contact-row"><span class="ic"><svg width="14" height="12" viewBox="0 0 14 12"><rect x="0" y="1" width="14" height="10" fill="#0c2252"/><path d="M0 1l7 5 7-5" stroke="#fff" fill="none"/></svg></span><span>info@claimshield.example</span></div>
  </div>
  <hr>
  <div class="copy">Copyrights@2023.Claim Shield All Rights Reserved</div>
  <span class="social" style="left:881px" aria-label="Social profile"></span>
  <span class="social" style="left:939px" aria-label="Social profile"></span>
  <span class="social" style="left:997px" aria-label="Social profile"></span>
  <span class="social" style="left:1055px" aria-label="Social profile"></span>
</footer>

</body>
</html>
```